QZSTREAMHUB ( Wordpress website for catalogue of Vorlo Stream Pages)

Need a website to showcase different Vorlo Stream pages ( in different categories). Similar to e-commerce except no check-out / purchase of items. Pls use our logos provided and color scheme to be white+red+ blue as per our logo.

Target Market(s)

Consumers

Font styles to use
Sans Serif

Colors
ffffff
ec1f27
3276b5

Requirements
Must have
• I will need a Wordpress Theme as a handover. Also, pls use the color scheme (red+blue+white) as per logo attached. Prefer clean and near design with white space.

```html
<!DOCTYPE html>
<html lang="en">
<head>
<meta charset="utf-8">
<title>QZSTREAMHUB – A Portal of Curated Vorlo Stream</title>
<link href="https://fonts.googleapis.com/css2?family=Roboto+Condensed:wght@400;700&family=Poppins:wght@400;500;600&family=Montserrat:wght@500;600&display=swap" rel="stylesheet">
<style>
:root{
  --red:#ec1f27;
  --blue:#3276b5;
  --white:#ffffff;
  --ink:#111111;
  --muted:#666666;
  --line:#e3e3e3;
  --hero:#9fcbf1;
  --footer:#1f1f21;
}
*{box-sizing:border-box;margin:0;padding:0}
html,body{width:1200px;height:4121px;overflow:hidden;background:var(--white)}
body{position:relative;font-family:'Poppins',sans-serif;color:var(--ink)}
.abs{position:absolute}
.ph{position:absolute;display:block}
/* top bar */
.topbar{position:absolute;left:0;top:0;width:1200px;height:48px;background:var(--red);color:var(--white);font-size:17px;font-weight:500}
.topbar .social{position:absolute;left:112px;top:13px;display:flex;gap:16px}
.topbar .social span{width:16px;height:16px;border:2px solid var(--white);border-radius:3px;display:block}
.topbar .contact{position:absolute;right:112px;top:12px;display:flex;gap:30px;align-items:center}
.topbar .contact svg{vertical-align:-3px;margin-right:6px}
/* nav */
.nav{position:absolute;left:0;top:48px;width:1200px;height:67px;background:var(--white);border-bottom:1px solid var(--line)}
.brand{position:absolute;left:109px;top:12px;font-family:'Montserrat',sans-serif;font-weight:600;font-size:36px;color:var(--blue);display:flex;align-items:center;gap:10px;letter-spacing:-0.5px}
.brand i{width:14px;height:14px;background:var(--red);display:block}
.menu{position:absolute;left:414px;top:24px;display:flex;gap:26px;font-family:'Roboto Condensed',sans-serif;font-weight:700;font-size:16px;color:var(--ink)}
.menu .on{color:var(--red)}
.search{position:absolute;left:914px;top:17px;width:175px;height:34px;border:1px solid #cfcfcf;font-size:14px;color:#888;padding:7px 9px}
.search b{position:absolute;right:0;top:0;width:28px;height:32px;background:var(--blue)}
.search b svg{margin:8px 6px}
/* hero */
.hero{position:absolute;left:0;top:115px;width:1200px;height:461px;background:var(--hero);overflow:hidden}
.hero-title{position:absolute;left:55px;top:140px;font-family:'Roboto Condensed',sans-serif;font-weight:700;font-size:78px;line-height:64px;color:#1a1a1a;letter-spacing:-1px}
.hero-title em{font-family:'Roboto Condensed',sans-serif;font-style:normal;font-weight:400;font-size:56px;color:var(--red)}
.hero-title .tag{display:inline-block;margin-top:10px;border:5px solid var(--red);color:var(--red);font-size:60px;line-height:56px;padding:0 8px}
.hero-art{left:380px;top:70px;width:820px;height:400px;background:linear-gradient(135deg,#c9e2f8,#7fb2e3 60%,#d8e9f7);border-radius:200px 0 0 0}
.stripe{position:absolute;top:576px;height:13px}
/* sections */
.h2{position:absolute;font-family:'Roboto Condensed',sans-serif;font-weight:700;font-size:38px;color:var(--ink);letter-spacing:-0.3px}
.card{position:absolute;width:303px;border:1px solid var(--line);background:var(--white)}
.card .date{position:absolute;left:0;top:138px;background:var(--blue);color:var(--white);font-size:12px;padding:6px 10px}
.card h3{font-family:'Montserrat',sans-serif;font-weight:600;font-size:18px;margin:0}
.cat{font-size:14px;color:var(--red)}
.txt{font-size:14px;line-height:28px;color:var(--muted);text-align:justify}
.more{font-family:'Poppins',sans-serif;font-weight:500;font-size:16px;color:var(--red)}
.stat{font-size:16px;color:#555}
.dotbtn{position:absolute;width:26px;height:26px;background:var(--red);border-radius:4px}
.news-title{font-family:'Montserrat',sans-serif;font-weight:600;font-size:20px;line-height:27px}
.meta{font-size:14px;color:#333}
/* category band */
.band{position:absolute;left:0;top:2501px;width:1200px;height:1251px;background:var(--blue);color:var(--white)}
.band .colt{position:absolute;top:92px;font-family:'Roboto Condensed',sans-serif;font-weight:700;font-size:32px}
.bitem{position:absolute;width:311px}
.bitem .ph{position:relative;width:311px;height:266px}
.bitem small{display:block;font-family:'Roboto Condensed',sans-serif;font-size:13px;margin-top:6px}
.bitem h4{font-family:'Roboto Condensed',sans-serif;font-weight:700;font-size:19px;margin-top:10px}
.bitem p{font-size:14px;line-height:28px;margin-top:6px;padding-left:2px}
.btn{display:inline-block;border-left:5px solid var(--red);border-right:5px solid var(--red);padding:2px;margin-top:16px}
.btn span{display:block;background:var(--red);color:var(--white);font-size:16px;font-weight:500;padding:8px 20px}
.rule{position:absolute;left:109px;width:979px;height:1px;background:rgba(255,255,255,.45)}
/* footer */
.footer{position:absolute;left:0;top:3752px;width:1200px;height:369px;background:var(--footer);color:var(--white)}
.footer .vline{position:absolute;top:40px;width:1px;height:180px;background:#555}
.footer h5{font-family:'Roboto Condensed',sans-serif;font-weight:700;font-size:18px}
.footer .fs{font-size:14px;line-height:29px}
.footer .bottom{position:absolute;left:109px;top:329px;width:979px;font-size:13px;display:flex;justify-content:space-between}
.footer .bottom nav{display:flex;gap:30px}
</style>
</head>
<body>

<header class="topbar">
  <div class="social" aria-label="Social links"><span></span><span></span><span></span><span></span></div>
  <div class="contact">
    <div><svg width="16" height="16" viewBox="0 0 24 24"><path fill="#fff" d="M6.6 10.8a15 15 0 0 0 6.6 6.6l2.2-2.2a1 1 0 0 1 1-.25 11.4 11.4 0 0 0 3.6.6 1 1 0 0 1 1 1V20a1 1 0 0 1-1 1A17 17 0 0 1 3 4a1 1 0 0 1 1-1h3.5a1 1 0 0 1 1 1c0 1.25.2 2.45.6 3.6a1 1 0 0 1-.25 1z"/></svg>555-010-0199</div>
    <div><svg width="18" height="14" viewBox="0 0 18 14"><rect x="1" y="1" width="16" height="12" fill="none" stroke="#fff" stroke-width="2"/><path d="M1 1l8 7 8-7" fill="none" stroke="#fff" stroke-width="2"/></svg>info@qzstreamhub.com</div>
  </div>
</header>

<nav class="nav">
  <div class="brand">QZSTREAMHUB<i></i></div>
  <div class="menu"><span class="on">HOME</span><span>ABOUT US</span><span>INSPIRE</span><span>SHOP</span><span>CATERGORIES</span><span>CONTACT</span></div>
  <div class="search">Search<b><svg width="16" height="16" viewBox="0 0 16 16"><circle cx="7" cy="7" r="5" fill="none" stroke="#fff" stroke-width="2"/><path d="M11 11l4 4" stroke="#fff" stroke-width="2"/></svg></b></div>
</nav>

<section class="hero">
  <div class="ph hero-art" role="img" aria-label="Illustration of a smartphone showing a live stream, with two shoppers carrying bags and boxes among food and fashion items"></div>
  <h1 class="hero-title">A PORTAL <em>of</em><br>CURATED<br>VORLO<br><span class="tag">STREAM</span></h1>
</section>
<div class="stripe" style="left:0;width:560px;background:var(--red)"></div>
<div class="stripe" style="left:560px;width:640px;background:var(--blue)"></div>

<!-- featured -->
<h2 class="h2" style="left:108px;top:690px">FEATURED POST</h2>

<article class="card" style="left:110px;top:757px;height:389px">
  <div class="ph" style="left:0;top:0;width:301px;height:174px;background:linear-gradient(135deg,#b9c6c9,#8a7256 55%,#d7cbb6)" role="img" aria-label="Photo of a seafood dish on a beach table"></div>
  <div class="date">▦ OCTOBER 9TH 2020</div>
  <div class="abs" style="left:10px;top:194px;width:282px">
    <h3>LOREM IPSUM DOLOR</h3>
    <div class="cat" style="margin-top:8px">CATEGORIES : Food</div>
    <p class="txt" style="margin-top:8px">Lorem ipsum dolor sit ,consectetur adipiscing elit. Praesent ultrices metus in orci eleifend lobortis.</p>
    <div style="display:flex;justify-content:space-between;margin-top:10px"><span class="more">READ MORE ➜</span><span class="stat">◉ 321 ◌ 41</span></div>
  </div>
</article>
<article class="card" style="left:448px;top:757px;height:389px">
  <div class="ph" style="left:0;top:0;width:301px;height:174px;background:linear-gradient(135deg,#a9b7c4,#d8bfa6 50%,#8b96a8)" role="img" aria-label="Photo of three friends laughing together"></div>
  <div class="date">▦ OCTOBER 17TH 2020</div>
  <div class="abs" style="left:10px;top:194px;width:282px">
    <h3>LOREM IPSUM DOLOR</h3>
    <div class="cat" style="margin-top:8px">CATEGORIES : Fashion</div>
    <p class="txt" style="margin-top:8px">Lorem ipsum dolor sit ,consectetur adipiscing elit. Praesent ultrices metus in orci eleifend lobortis.</p>
    <div style="display:flex;justify-content:space-between;margin-top:10px"><span class="more">READ MORE ➜</span><span class="stat">◉ 321 ◌ 41</span></div>
  </div>
</article>
<article class="card" style="left:785px;top:757px;height:389px">
  <div class="ph" style="left:0;top:0;width:301px;height:174px;background:linear-gradient(135deg,#8f8f8a,#c4a88a 55%,#6d7c85)" role="img" aria-label="Photo of a traveller in a busy street market"></div>
  <div class="date">▦ SEPTEMBER 9TH 2020</div>
  <div class="abs" style="left:10px;top:194px;width:282px">
    <h3>LOREM IPSUM DOLOR</h3>
    <div class="cat" style="margin-top:8px">CATEGORIES : Fashion</div>
    <p class="txt" style="margin-top:8px">Lorem ipsum dolor sit ,consectetur adipiscing elit. Praesent ultrices metus in orci eleifend lobortis.</p>
    <div style="display:flex;justify-content:space-between;margin-top:10px"><span class="more">READ MORE ➜</span><span class="stat">◉ 321 ◌ 41</span></div>
  </div>
</article>

<!-- latest news -->
<h2 class="h2" style="left:109px;top:1228px">LATEST NEWS</h2>
<div class="ph" style="left:112px;top:1298px;width:459px;height:362px;background:linear-gradient(135deg,#6d7c5c,#b8443b 45%,#e3c7a5 70%,#3e4a56)" role="img" aria-label="Photo of friends in winter clothes opening a gift"></div>
<div class="abs" style="left:137px;top:1684px;width:420px">
  <div class="news-title" style="font-size:22px">The standard Lorem Ipsum passage, used since the 1500s</div>
  <div class="meta" style="margin-top:18px">october - 28 - 2020 • Featured</div>
  <p class="txt" style="margin-top:20px;font-size:14px;line-height:26px">"Lorem ipsum dolor sit amet, consectetur adipiscing elit, sed do eiusmod tempor incididunt ut labore et dolore magna aliqua. Ut enim ad minim veniam,</p>
  <div class="more" style="margin-top:14px">READ MORE ➜</div>
</div>

<div class="ph" style="left:597px;top:1296px;width:190px;height:189px;background:linear-gradient(180deg,#f0c27a,#5e7c8f 55%,#3d5a4a)" role="img" aria-label="Photo of a sunset over hills"></div>
<div class="abs" style="left:811px;top:1302px;width:280px">
  <div class="news-title">The standard Lorem Ipsum passage, used since</div>
  <div class="meta" style="margin-top:16px">June - 02 - 2020 • Featured</div>
  <p class="txt" style="margin-top:12px;font-size:13px;line-height:26px">"Lorem ipsum dolor amet, consectetur adipiscing elit, sed do eiusmod ..</p>
</div>
<div class="ph" style="left:597px;top:1512px;width:190px;height:187px;background:linear-gradient(180deg,#e9d2b2,#7a8a94 55%,#b59a7a)" role="img" aria-label="Photo of a person resting on a beach at sunset"></div>
<div class="abs" style="left:811px;top:1517px;width:280px">
  <div class="news-title">The standard Lorem Ipsum passage, used since</div>
  <div class="meta" style="margin-top:16px">September - 11 - 2020 • Featured</div>
  <p class="txt" style="margin-top:12px;font-size:13px;line-height:26px">"Lorem ipsum dolor amet, consectetur adipiscing elit, sed do eiusmod ..</p>
</div>
<div class="ph" style="left:597px;top:1726px;width:190px;height:188px;background:linear-gradient(135deg,#c6b89c,#b0473d 45%,#3d3a3a)" role="img" aria-label="Photo of friends walking together in a city"></div>
<div class="abs" style="left:811px;top:1732px;width:280px">
  <div class="news-title">The standard Lorem Ipsum passage, used since</div>
  <div class="meta" style="margin-top:16px">May - 03 - 2020 • Featured</div>
  <p class="txt" style="margin-top:12px;font-size:13px;line-height:26px">"Lorem ipsum dolor amet, consectetur adipiscing elit, sed do eiusmod ..</p>
</div>

<!-- recent foods -->
<h2 class="h2" style="left:109px;top:1991px">RECENT INSPIRED FOODS</h2>

<article class="card" style="left:110px;top:2066px;height:345px">
  <div class="ph" style="left:0;top:0;width:301px;height:193px;background:linear-gradient(135deg,#c9b58b,#d9562e 50%,#f0c54a)" role="img" aria-label="Photo of a crab and fries platter"></div>
  <div class="abs" style="left:10px;top:202px;width:280px">
    <div style="display:flex;justify-content:space-between"><span class="cat" style="margin-top:6px">Food</span><span class="stat">◉ 321 ◌ 41</span></div>
    <h3>LOREM IPSUM DOLOR</h3>
    <p class="txt" style="margin-top:6px;font-size:13px">Lorem ipsum dolor sit amet, consectetur adipiscing elit, sed do eiusmod tempor incididunt ut labore</p>
  </div>
  <span class="dotbtn" style="right:1px;bottom:1px"></span>
</article>
<article class="card" style="left:447px;top:2066px;height:345px">
  <div class="ph" style="left:0;top:0;width:301px;height:193px;background:linear-gradient(135deg,#3d3f45,#7a5a48 50%,#202228)" role="img" aria-label="Photo of a woman eating noodles with chopsticks"></div>
  <div class="abs" style="left:10px;top:202px;width:280px">
    <div style="display:flex;justify-content:space-between"><span class="cat" style="margin-top:6px">Food</span><span class="stat">◉ 321 ◌ 41</span></div>
    <h3>LOREM IPSUM DOLOR</h3>
    <p class="txt" style="margin-top:6px;font-size:13px">Lorem ipsum dolor sit amet, consectetur adipiscing elit, sed do eiusmod tempor incididunt ut labore</p>
  </div>
  <span class="dotbtn" style="right:1px;bottom:1px"></span>
</article>
<article class="card" style="left:782px;top:2066px;height:345px">
  <div class="ph" style="left:0;top:0;width:301px;height:193px;background:linear-gradient(135deg,#c9c2b2,#d8614a 45%,#8a9a6a)" role="img" aria-label="Photo of a couple sharing a salad"></div>
  <div class="abs" style="left:10px;top:202px;width:280px">
    <div style="display:flex;justify-content:space-between"><span class="cat" style="margin-top:6px">Food</span><span class="stat">◉ 321 ◌ 41</span></div>
    <h3>LOREM IPSUM DOLOR</h3>
    <p class="txt" style="margin-top:6px;font-size:13px">Lorem ipsum dolor sit amet, consectetur adipiscing elit, sed do eiusmod tempor incididunt ut labore</p>
  </div>
  <span class="dotbtn" style="right:1px;bottom:1px"></span>
</article>

<!-- category band -->
<section class="band">
  <div class="colt" style="left:109px">FOOD</div>
  <div class="colt" style="left:442px">TECHNOLOGY</div>
  <div class="colt" style="left:780px">FASHION</div>

  <div class="bitem" style="left:109px;top:131px">
    <div class="ph" style="background:linear-gradient(135deg,#9a9a92,#c9a488 50%,#5e6a6a)" role="img" aria-label="Photo of a couple sharing pizza on city steps"></div>
    <small>Food</small><h4>LOREM IPSUM DOLOR SIT</h4>
    <p>Lorem ipsum dolor sit amet, conseptur adipiscing elit, sed do eiusmod</p>
    <div class="btn"><span>MORE DETAILS</span></div>
  </div>
  <div class="bitem" style="left:442px;top:131px">
    <div class="ph" style="background:linear-gradient(135deg,#a7a49c,#6e6c6a 50%,#c4bfb5)" role="img" aria-label="Photo of a person using a phone in a street with floating interface panels"></div>
    <small>Technology</small><h4>LOREM IPSUM DOLOR SIT</h4>
    <p>Lorem ipsum dolor sit amet, conseptur adipiscing elit, sed do eiusmod</p>
    <div class="btn"><span>MORE DETAILS</span></div>
  </div>
  <div class="bitem" style="left:776px;top:131px">
    <div class="ph" style="background:linear-gradient(135deg,#b9cde0,#8fa2b8 50%,#d1b07a)" role="img" aria-label="Photo of a shopper with bags in front of city towers"></div>
    <small>Fashion</small><h4>LOREM IPSUM DOLOR SIT</h4>
    <p>Lorem ipsum dolor sit amet, conseptur adipiscing elit, sed do eiusmod</p>
    <div class="btn"><span>MORE DETAILS</span></div>
  </div>

  <div class="rule" style="top:599px"></div>

  <div class="bitem" style="left:109px;top:630px">
    <div class="ph" style="background:linear-gradient(135deg,#6b5a4a,#d9c2a0 50%,#8a6b4e)" role="img" aria-label="Photo of plates of oysters and seafood on a table"></div>
    <small>Food</small><h4>LOREM IPSUM DOLOR SIT</h4>
    <p>Lorem ipsum dolor sit amet, conseptur adipiscing elit, sed do eiusmod</p>
    <div class="btn"><span>MORE DETAILS</span></div>
  </div>
  <div class="bitem" style="left:442px;top:630px">
    <div class="ph" style="background:linear-gradient(135deg,#c7c2b8,#8d8a86 50%,#e0ddd6)" role="img" aria-label="Photo of a hand holding a phone showing a city map"></div>
    <small>Technology</small><h4>LOREM IPSUM DOLOR SIT</h4>
    <p>Lorem ipsum dolor sit amet, conseptur adipiscing elit, sed do eiusmod</p>
    <div class="btn"><span>MORE DETAILS</span></div>
  </div>
  <div class="bitem" style="left:776px;top:630px">
    <div class="ph" style="background:linear-gradient(135deg,#5c4e48,#a9867a 50%,#3c4656)" role="img" aria-label="Photo of a woman browsing clothes in a shop"></div>
    <small>Fashion</small><h4>LOREM IPSUM DOLOR SIT</h4>
    <p>Lorem ipsum dolor sit amet, conseptur adipiscing elit, sed do eiusmod</p>
    <div class="btn"><span>MORE DETAILS</span></div>
  </div>

  <div class="rule" style="top:1107px"></div>

  <div class="abs" style="left:109px;top:1114px"><div class="btn"><span style="padding:8px 30px">VIEW MORE POSTS</span></div></div>
  <div class="abs" style="left:442px;top:1114px"><div class="btn"><span style="padding:8px 30px">VIEW MORE POSTS</span></div></div>
  <div class="abs" style="left:774px;top:1114px"><div class="btn"><span style="padding:8px 30px">VIEW MORE POSTS</span></div></div>
</section>

<!-- footer -->
<footer class="footer">
  <div class="abs" style="left:112px;top:102px;font-family:'Montserrat',sans-serif;font-weight:600;font-size:27px;color:var(--blue)">QZSTREAMHUB</div>
  <div class="vline" style="left:296px"></div>
  <div class="abs" style="left:322px;top:84px;width:230px">
    <h5>CONTACT</h5>
    <div class="fs" style="margin-top:4px;display:flex;gap:8px"><svg width="12" height="16" viewBox="0 0 12 16" style="margin-top:6px;flex:none"><path fill="#ec1f27" d="M6 0a6 6 0 0 0-6 6c0 4.5 6 10 6 10s6-5.5 6-10a6 6 0 0 0-6-6zm0 8.5A2.5 2.5 0 1 1 6 3.5a2.5 2.5 0 0 1 0 5z"/></svg><span>12 Harbour Lane #02-07<br>Parkside Hub, Singapore 000000</span></div>
    <div class="fs" style="margin-top:8px;display:flex;gap:8px;align-items:center"><svg width="14" height="14" viewBox="0 0 24 24"><path fill="#ec1f27" d="M6.6 10.8a15 15 0 0 0 6.6 6.6l2.2-2.2a1 1 0 0 1 1-.25 11.4 11.4 0 0 0 3.6.6 1 1 0 0 1 1 1V20a1 1 0 0 1-1 1A17 17 0 0 1 3 4a1 1 0 0 1 1-1h3.5a1 1 0 0 1 1 1c0 1.25.2 2.45.6 3.6a1 1 0 0 1-.25 1z"/></svg>555-010-0199</div>
    <div class="fs" style="margin-top:8px;display:flex;gap:8px;align-items:center"><svg width="14" height="11" viewBox="0 0 18 14"><rect x="1" y="1" width="16" height="12" fill="none" stroke="#ec1f27" stroke-width="2"/><path d="M1 1l8 7 8-7" fill="none" stroke="#ec1f27" stroke-width="2"/></svg>info@qzstreamhub.com</div>
  </div>
  <div class="vline" style="left:547px"></div>
  <div class="abs" style="left:572px;top:92px;width:280px">
    <h5>NEWSLETTER SIGNUP</h5>
    <p class="fs" style="margin-top:8px;font-size:13px;line-height:26px">Join our comunity and receive latest news &amp; updates about our company and our offer</p>
    <div style="position:relative;margin-top:12px;width:267px;height:40px;background:#fff;color:#888;font-size:13px;padding:10px 12px">Email
      <span style="position:absolute;right:2px;top:2px;width:42px;height:36px;background:var(--red)"><svg width="20" height="20" viewBox="0 0 20 20" style="margin:8px 11px"><path d="M2 9l16-7-6 16-3-7z" fill="none" stroke="#fff" stroke-width="2"/></svg></span>
    </div>
  </div>
  <div class="vline" style="left:866px"></div>
  <div class="abs" style="left:889px;top:106px;width:220px">
    <h5>FOLLOW US</h5>
    <p class="fs" style="margin-top:8px;font-size:13px;line-height:24px">Visit &amp; Follow QZSTREAMHUB<br>at our social media accounts</p>
    <div style="display:flex;gap:10px;margin-top:10px"><span style="width:12px;height:12px;border:2px solid #fff;border-radius:3px"></span><span style="width:12px;height:12px;border:2px solid #fff;border-radius:3px"></span><span style="width:12px;height:12px;border:2px solid #fff;border-radius:3px"></span><span style="width:12px;height:12px;border:2px solid #fff;border-radius:3px"></span><span style="width:12px;height:12px;border:2px solid #fff;border-radius:3px"></span></div>
  </div>
  <div class="bottom">
    <span>© 2020 COPYRIGHT QZSTREAMHUB &nbsp;IMPRINT &nbsp;PRIVACY</span>
    <nav><span>Home</span><span>About Us</span><span>Inspire</span><span>Shop</span><span>Catergories</span><span>Contact</span></nav>
  </div>
</footer>

</body>
</html>
```